RW Framewell Inc Business cards

We need business cards using our existing logo but slightly modified. Right now the logo says RW Loadbearing Masonry. We want to keep the RW part of the design, but replace the Structural Concrete portion with "FRAMEWELL". Please see the attached file.
Ideally this would be a blank template so we can add Different Names, titles, and phone numbers later.
On the one side we want only the logo and on the other side the detail. I'm attaching an example for you to see.
Please reach out with any other questions. Our address and other details will be given out once we find a design we like.

Target Market(s)

Construction Industry

```html
<!DOCTYPE html>
<html lang="en">
<head>
<meta charset="utf-8">
<title>RW Framewell Inc – Business Cards</title>
<link rel="stylesheet" href="https://fonts.googleapis.com/css2?family=Montserrat:wght@600;700&family=Roboto:wght@400;500&display=swap">
<style>
  :root {
    --stage: #3a3a3c;
    --card: #1c1c1e;
    --brand-blue: #2e64ad;
    --wave-grey: #7a7a7c;
    --wave-black: #0e0e0f;
    --text-light: #ffffff;
    --text-muted: #e6e6e6;
  }
  * { box-sizing: border-box; margin: 0; padding: 0; }
  html, body {
    width: 799px; height: 1200px; overflow: hidden;
    background: var(--stage);
    font-family: "Roboto", Arial, sans-serif;
  }
  .sheet {
    width: 799px; height: 1200px;
    display: flex; flex-direction: column; align-items: center; justify-content: space-around;
    padding: 70px 0;
  }
  .card {
    position: relative;
    width: 640px; height: 366px;
    background: var(--card);
    border-radius: 4px;
    overflow: hidden;
    box-shadow: 0 18px 30px rgba(0,0,0,0.45);
  }
  .wordmark {
    display: flex; align-items: center; gap: 14px;
    font-family: "Montserrat", Arial, sans-serif;
    font-weight: 700;
    color: var(--brand-blue);
    letter-spacing: 0.08em;
    text-transform: uppercase;
  }
  .wordmark-square {
    background: var(--brand-blue);
    flex: none;
  }
  .card-front .wordmark {
    position: absolute; left: 50%; top: 50%;
    transform: translate(-50%, -50%);
    font-size: 44px;
  }
  .card-front .wordmark-square { width: 34px; height: 34px; }

  .card-back .wordmark {
    position: absolute; right: 40px; top: 118px;
    font-size: 27px;
  }
  .card-back .wordmark-square { width: 22px; height: 22px; }

  .waves { position: absolute; left: 0; top: 0; width: 640px; height: 366px; }

  .identity { position: absolute; left: 40px; top: 44px; }
  .person-name {
    font-family: "Montserrat", Arial, sans-serif;
    font-weight: 600; font-size: 19px;
    color: var(--brand-blue);
  }
  .person-title { font-size: 13px; color: var(--text-muted); margin-top: 3px; }

  .address {
    position: absolute; left: 40px; top: 122px;
    font-size: 14px; line-height: 1.45;
    color: var(--text-light);
  }

  .contact {
    position: absolute; right: 40px; bottom: 34px;
    list-style: none;
    font-size: 15px; line-height: 1.55;
    color: var(--text-light);
    text-align: right;
  }
  .contact li { display: flex; align-items: center; justify-content: flex-end; gap: 10px; }
  .contact svg { width: 14px; height: 14px; fill: var(--text-light); flex: none; }
</style>
</head>
<body>
<main class="sheet">

  <section class="card card-front" aria-label="Business card front">
    <div class="wordmark">
      <span class="wordmark-square"></span>
      <span>RW Framewell</span>
    </div>
  </section>

  <section class="card card-back" aria-label="Business card back">
    <svg class="waves" viewBox="0 0 640 366" aria-hidden="true">
      <path d="M0 176 C120 230 280 270 420 262 C520 256 590 236 640 222 L640 366 L0 366 Z" fill="var(--wave-grey)"/>
      <path d="M0 190 C120 246 280 282 420 276 C520 272 590 252 640 238 L640 366 L0 366 Z" fill="var(--wave-black)"/>
      <path d="M0 214 C140 262 250 270 360 262 C470 254 560 244 640 252 L640 366 L0 366 Z" fill="var(--wave-grey)"/>
      <path d="M0 226 C150 272 260 280 370 272 C480 264 570 258 640 266 L640 366 L0 366 Z" fill="var(--brand-blue)"/>
    </svg>

    <div class="identity">
      <p class="person-name">Daniel RW Porter</p>
      <p class="person-title">Managing Director</p>
    </div>

    <p class="address">58 Foundry Lane, Millbrook,<br>Oregon, US 97321</p>

    <div class="wordmark">
      <span class="wordmark-square"></span>
      <span>RW Framewell</span>
    </div>

    <ul class="contact">
      <li>541-555-0142
        <svg viewBox="0 0 24 24"><path d="M6.6 10.8a15.1 15.1 0 0 0 6.6 6.6l2.2-2.2a1 1 0 0 1 1-.25 11.4 11.4 0 0 0 3.6.57 1 1 0 0 1 1 1V20a1 1 0 0 1-1 1A17 17 0 0 1 3 4a1 1 0 0 1 1-1h3.5a1 1 0 0 1 1 1c0 1.25.2 2.45.57 3.57a1 1 0 0 1-.25 1z"/></svg>
      </li>
      <li>daniel@framewellbuild.com
        <svg viewBox="0 0 24 24"><path d="M2 5h20v14H2z M3.5 6.5 12 13l8.5-6.5" fill="none" stroke="#fff" stroke-width="2"/></svg>
      </li>
      <li>framewellbuild.com
        <svg viewBox="0 0 24 24"><circle cx="12" cy="12" r="9" fill="none" stroke="#fff" stroke-width="2"/><path d="M3 12h18M12 3c3 3 3 15 0 18M12 3c-3 3-3 15 0 18" fill="none" stroke="#fff" stroke-width="1.6"/></svg>
      </li>
    </ul>
  </section>

</main>
</body>
</html>
```